Web Page Design for a Website that Provides Tutoring

I am looking to create an online tutoring website. The website will allow parents or students to contact tutors with a view to instructing them to tutor themselves or their children.

The name of the website is LendYourLessons.

This brief is to create the design for one of the web pages for this web site. I am hoping the same designer will be available to design other pages.

The page I want designed is one of the more complex and I have attached the design as an excel spreadsheet. The web page needs to include all the items on this page but if you want to change the positioning of the items then Im fine with that.

I recently had two logos created for this website. My favourite is the one with a mortar board but im not sure I like the colours. I have attached both of these logos and you can use either of them, change the colours or create something different. I just want a design pleasing to the eye. If the logo is changed I would like that in a seperate file.

So can you please submit designs for this page. I have attached the two logos which you can use, change or if you feel you have a better idea then you can use that.

On the spreadsheet the Send Message, Favourite etc are buttons.

Target Market(s)

People who want to better themselves.
Possible middle class to upper class.

Industry/Entity Type

Tutoring

Number of Pages Required

1 page

Requirements
Must have
• The designs must have alot of the information attached in the spreadsheet.

```html
<!DOCTYPE html>
<html lang="en">
<head>
<meta charset="utf-8">
<title>LendYourLessons – Tutor Profile</title>
<link rel="stylesheet" href="https://fonts.googleapis.com/css2?family=Oxygen:wght@400;700&family=Roboto+Slab:wght@300;400&family=Cabin+Sketch:wght@700&display=swap">
<style>
:root{
  --navy:#23253d;
  --navy-line:#33364f;
  --orange:#f07b16;
  --yellow:#f0b400;
  --green:#35a882;
  --purple:#575a8e;
  --red:#e8100f;
  --ink:#333;
  --grey:#e4e4e4;
  --field:#e9e9e9;
  --line:#e6e6e6;
  --avail:#d6fdd6;
  --taken:#fd6540;
  --reserved:#f7941d;
  --no:#35578f;
  --chalk:#3fb48a;
}
*{box-sizing:border-box;margin:0;padding:0}
html,body{width:1200px;height:2651px;overflow:hidden}
body{position:relative;background:#fff;font-family:"Oxygen",sans-serif;color:var(--ink);font-size:13px}
.abs{position:absolute}
.slab{font-family:"Roboto Slab",serif}
.hero-band{left:0;top:0;width:1200px;height:592px;background:var(--navy)}
.nav{left:0;top:0;width:1200px;height:74px;border-bottom:1px solid var(--navy-line)}
.brand{position:absolute;left:74px;top:18px;display:flex;align-items:center;gap:6px;color:var(--orange);font-weight:700;font-size:28px;letter-spacing:-.5px}
.brand-dot{width:12px;height:12px;border-radius:50%;background:var(--orange)}
.menu{position:absolute;left:410px;top:28px;display:flex;gap:30px;color:#fff;font-size:14px}
.menu .active{border-bottom:2px solid var(--orange);padding-bottom:6px}
.login{position:absolute;right:74px;top:28px;color:#fff;font-size:14px;display:flex;align-items:center;gap:8px}
.hero-photo{left:134px;top:124px;width:340px;height:341px;border:5px solid #fff;background:linear-gradient(160deg,#c9c2b6,#7d7c80 60%,#3e4452)}
.hi-bubble{left:535px;top:128px;width:102px;height:124px}
.hi-text{left:535px;top:136px;width:102px;text-align:center;color:#fff;font-family:"Roboto Slab",serif;font-size:42px;font-weight:300;line-height:80px}
.hero-name{left:652px;top:136px;color:var(--chalk);font-family:"Cabin Sketch",sans-serif;font-weight:700;font-size:50px;line-height:60px}
.hero-iam{left:654px;top:206px;color:#fff;font-family:"Roboto Slab",serif;font-weight:300;font-size:34px;line-height:44px}
.hero-bio{left:654px;top:272px;width:420px;color:#e6e6ee;font-size:15px;line-height:24px}
.btn{display:flex;align-items:center;justify-content:center;gap:8px;color:#fff;font-size:14px;text-transform:uppercase}
.hero-btn{top:406px;height:42px;border-radius:2px}
.hero-btn.register{left:656px;width:190px;background:var(--orange)}
.hero-btn.video{left:856px;width:194px;background:var(--green)}
.card-wrap{left:74px;top:521px;width:1052px;height:341px;background:#fff}
.card{top:535px;width:331px;height:324px;border:4px solid}
.card h3{height:52px;line-height:52px;padding-left:14px;color:#fff;font-family:"Roboto Slab",serif;font-weight:300;font-size:21px}
.card.contact{left:88px;border-color:var(--yellow)}.card.contact h3{background:var(--yellow)}
.card.fav{left:435px;border-color:var(--green)}.card.fav h3{background:var(--green)}
.card.reviews{left:781px;border-color:var(--purple)}.card.reviews h3{background:var(--purple)}
.card-body{padding:20px 24px 0}
.field{background:var(--field);color:#999;font-size:13px;padding:12px 14px;margin-bottom:8px}
.field.subject{height:42px}.field.msg{height:110px}
.card-btn{height:42px;margin-top:14px}
.contact .card-btn{background:var(--yellow)}
.fav .card-btn{background:var(--green);margin-top:22px}
.reviews .card-btn{background:var(--purple);margin-top:12px}
.fav-lead{font-weight:700;font-size:14px;line-height:20px;margin-bottom:12px;width:220px}
.ticks li{list-style:none;display:flex;align-items:center;gap:10px;font-size:13px;height:27px}
.stars{color:var(--yellow);letter-spacing:1px;font-size:15px}
.stars .off{color:#ccc}
.rev-head{display:flex;align-items:center;gap:8px;font-size:12px;margin-bottom:12px}
.bar-row{display:flex;align-items:center;font-size:12px;height:20px}
.bar-row span:first-child{width:50px}
.bar{width:110px;height:9px;background:var(--grey);margin-right:14px}
.bar i{display:block;height:100%;background:var(--yellow)}
.rev-note{font-size:13px;margin-top:6px}
.panel-head{height:53px;background:var(--navy);color:#fff;font-family:"Roboto Slab",serif;font-weight:300;font-size:22px;line-height:53px;padding-left:18px}
.scoring{left:74px;top:889px;width:511px;height:221px;border:1px solid var(--line)}
.score-row{display:flex;align-items:center;height:56px;margin:0 16px;border-bottom:1px solid var(--line);font-size:13px}
.score-row:last-child{border-bottom:0}
.score-row .lbl{width:154px}
.score-row .val{width:180px;display:flex;align-items:center}
.score-row .val b{font-weight:400;margin-left:8px}
.feedback{background:var(--red);color:#fff;font-size:13px;height:32px;width:142px;border-radius:2px;display:flex;align-items:center;justify-content:center;gap:6px;margin-left:auto}
.tutor-info{left:613px;top:889px;width:513px;height:221px;border:1px solid var(--line)}
.info-row{display:flex;align-items:center;height:56px;margin:0 18px;border-bottom:1px solid var(--line);font-size:13px}
.info-row.head{height:53px;margin:0;padding:0 18px;background:var(--grey);border:0}
.info-row:last-child{border-bottom:0}
.info-row span:nth-child(1){width:180px}.info-row span:nth-child(2){width:175px}
.subjects{left:74px;top:1140px;width:1052px;height:336px;border:1px solid var(--line)}
.subj-row{display:flex;align-items:center;height:56px;margin:0 0 0 16px;border-bottom:1px solid var(--line);font-size:13px}
.subj-row.head{height:53px;margin:0;padding-left:16px;background:var(--grey);border:0}
.subj-row:last-child{border-bottom:0}
.subj-row span{width:126px}
.subj-row span:first-child{width:210px}
.subj-row span:nth-child(3){width:143px}
.subj-row span:nth-child(4){width:110px}
.subj-row span:nth-child(5){width:120px}
.subj-row span:nth-child(6){width:141px}
.availability{left:74px;top:1505px;width:1052px;height:329px;border:1px solid var(--line)}
.avail-head{display:flex;justify-content:space-between;padding-right:18px}
.month{display:flex;align-items:center;gap:12px;font-size:21px}
.grid{display:grid;grid-template-columns:repeat(8,1fr);font-size:13px}
.grid div{height:53px;display:flex;align-items:center;justify-content:center;border-right:1px solid #fff;border-bottom:1px solid #fff}
.grid .h{background:var(--grey);height:51px}
.grid .t{background:#eee}
.grid .a{background:var(--avail)}.grid .tk{background:var(--taken)}.grid .r{background:var(--reserved)}.grid .n{background:var(--no)}
.legend{display:flex;justify-content:center;gap:34px;height:64px;align-items:center;font-size:13px}
.legend span{display:flex;align-items:center;gap:10px}
.legend i{display:block;width:18px;height:18px}
.section-title{left:0;top:1872px;width:1200px;text-align:center;font-family:"Roboto Slab",serif;font-weight:300;font-size:22px;color:var(--ink)}
.title-rule{left:584px;top:1912px;width:32px;height:3px;background:var(--orange)}
.review-card{top:2014px;width:332px;height:253px;background:#f2f2f2;text-align:center}
.avatar{position:absolute;left:128px;top:-38px;width:76px;height:76px;border:3px solid #fff}
.review-card h4{margin-top:62px;font-family:"Roboto Slab",serif;font-weight:400;font-size:18px}
.review-card .stars{font-size:15px;margin-top:4px}
.review-card small{display:block;font-size:11px;margin-top:4px}
.review-card p{font-size:13px;line-height:20px;margin:16px 36px 0}
.footer{left:0;top:2325px;width:1200px;height:326px;background:var(--navy);color:#fff}
.fcol{position:absolute;top:42px}
.fcol h5{font-family:"Roboto Slab",serif;font-weight:400;font-size:18px;margin-bottom:14px}
.fcol p,.fcol li{font-size:13px;line-height:26px;list-style:none;color:#e8e8ee}
.news p{line-height:20px}
.news label{display:block;font-size:13px;border-bottom:1px solid #fff;width:244px;padding:10px 0 6px}
.subscribe{width:244px;height:36px;background:var(--green);margin-top:20px;font-size:13px}
.social{display:flex;gap:6px;margin-top:20px}
.social i{width:34px;height:34px;border-radius:50%;display:block}
.copy{position:absolute;left:0;top:276px;width:1200px;text-align:center;font-size:13px;color:#e8e8ee}
</style>
</head>
<body>
<div class="abs hero-band"></div>
<header class="abs nav">
  <div class="brand"><span class="brand-dot"></span>LendYourLessons</div>
  <nav class="menu"><span class="active">HOME</span><span>SEARCH</span><span>STUDENT</span><span>TUTOR</span><span>ABOUT</span><span>CONTACT</span></nav>
  <div class="login"><svg width="14" height="14" viewBox="0 0 14 14"><circle cx="7" cy="4" r="3.5" fill="#f07b16"/><path d="M0 14c0-4 3-6 7-6s7 2 7 6z" fill="#f07b16"/></svg>LOGIN OR REGISTER</div>
</header>

<div class="abs hero-photo" role="img" aria-label="Portrait photo of the tutor in a grey suit"></div>
<svg class="abs hi-bubble" viewBox="0 0 102 124"><circle cx="51" cy="50" r="50" fill="#f07b16"/><path d="M20 86 L10 124 L48 98 z" fill="#f07b16"/></svg>
<div class="abs hi-text">Hi.</div>
<div class="abs hero-name">My name is Maddie</div>
<div class="abs hero-iam">I am....</div>
<p class="abs hero-bio">Passionate about teaching. I Find it easy to inspire children to want learn, a gift not many people have. I am excellent English Teachear and Understand the letest teaching practices.</p>
<div class="abs btn hero-btn register"><svg width="14" height="14" viewBox="0 0 14 14"><path d="M2 10l7-7 2 2-7 7H2z" fill="#fff"/></svg>Register Today</div>
<div class="abs btn hero-btn video"><svg width="16" height="12" viewBox="0 0 16 12"><rect x="0" y="1" width="11" height="10" rx="1" fill="#fff"/><path d="M11 6l5-4v8z" fill="#fff"/></svg>Watch Our Video</div>

<div class="abs card-wrap"></div>
<section class="abs card contact">
  <h3>Contact Us</h3>
  <div class="card-body">
    <div class="field subject">Subject</div>
    <div class="field msg">Messages</div>
    <div class="btn card-btn"><svg width="18" height="12" viewBox="0 0 18 12"><path d="M4 0h14L11 6z M4 2l7 5 7-5v10H4z" fill="#fff"/><rect x="0" y="4" width="3" height="1.5" fill="#fff"/><rect x="0" y="7" width="3" height="1.5" fill="#fff"/></svg>Send Message</div>
  </div>
</section>
<section class="abs card fav">
  <h3>Contact Favour</h3>
  <div class="card-body">
    <p class="fav-lead">She Would like to know your schedule.</p>
    <ul class="ticks">
      <li><svg width="14" height="14" viewBox="0 0 14 14"><rect x="1" y="1" width="12" height="12" fill="none" stroke="#35a882" stroke-width="1.5"/><path d="M3.5 7l2.5 2.5 5-5" fill="none" stroke="#35a882" stroke-width="1.8"/></svg>Offline Lessons</li>
      <li><svg width="14" height="14" viewBox="0 0 14 14"><rect x="1" y="1" width="12" height="12" fill="none" stroke="#35a882" stroke-width="1.5"/><path d="M3.5 7l2.5 2.5 5-5" fill="none" stroke="#35a882" stroke-width="1.8"/></svg>Affordable Rates</li>
      <li><svg width="14" height="14" viewBox="0 0 14 14"><rect x="1" y="1" width="12" height="12" fill="none" stroke="#35a882" stroke-width="1.5"/><path d="M3.5 7l2.5 2.5 5-5" fill="none" stroke="#35a882" stroke-width="1.8"/></svg>1-on-1 Tutoring</li>
      <li><svg width="14" height="14" viewBox="0 0 14 14"><rect x="1" y="1" width="12" height="12" fill="none" stroke="#35a882" stroke-width="1.5"/><path d="M3.5 7l2.5 2.5 5-5" fill="none" stroke="#35a882" stroke-width="1.8"/></svg>Refund Policy</li>
    </ul>
    <div class="btn card-btn"><svg width="14" height="14" viewBox="0 0 14 14"><circle cx="7" cy="4" r="3.5" fill="#fff"/><path d="M0 14c0-4 3-6 7-6s7 2 7 6z" fill="#fff"/></svg>Contact Favour</div>
  </div>
</section>
<section class="abs card reviews">
  <h3>Customer Reviews</h3>
  <div class="card-body">
    <div class="rev-head"><span class="stars">★★★★★</span><span>15 (5.0 out of 5 stars)</span></div>
    <div class="bar-row"><span>5 Star</span><span class="bar"><i style="width:100%"></i></span><span>100%</span></div>
    <div class="bar-row"><span>4 Star</span><span class="bar"></span><span>0%</span></div>
    <div class="bar-row"><span>3 Star</span><span class="bar"></span><span>0%</span></div>
    <div class="bar-row"><span>2 Star</span><span class="bar"></span><span>0%</span></div>
    <div class="bar-row"><span>1 Star</span><span class="bar"></span><span>0%</span></div>
    <p class="rev-note">Share your thoughts with other customers</p>
    <div class="btn card-btn"><svg width="14" height="14" viewBox="0 0 14 14"><path d="M2 10l7-7 2 2-7 7H2z" fill="#fff"/></svg>Write a Review</div>
  </div>
</section>

<section class="abs scoring">
  <div class="panel-head">Scoring</div>
  <div class="score-row"><span class="lbl">Review Score</span><span class="val"><span class="stars">★★★★<span class="off">★</span></span><b>4.5/5</b></span><span>Member Since</span></div>
  <div class="score-row"><span class="lbl">Reliability</span><span class="val"><span class="stars">★★★★<span class="off">★</span></span><b>4.0/5</b></span><span>Last Logged In</span></div>
  <div class="score-row"><span class="lbl">Punctuality</span><span class="val"><span class="stars">★★★★<span class="off">★</span></span><b>4.6/5</b></span><span class="feedback"><svg width="12" height="12" viewBox="0 0 12 12"><path d="M0 5L12 0 8 12 6 7z" fill="#fff"/></svg>Leave Feedback</span></div>
</section>
<section class="abs tutor-info">
  <div class="info-row head"><span>Tutoring Type</span><span>In Personal Only</span><span>Teacher</span></div>
  <div class="info-row"><span>Willing To Travel</span><span>Home Only</span><span>Full Time Tutor</span></div>
  <div class="info-row"><span>Age</span><span>20</span><span>Full Time Student</span></div>
  <div class="info-row"><span>DBS (CRB)</span><span></span><span></span></div>
</section>

<section class="abs subjects">
  <div class="panel-head">Subject Taught</div>
  <div class="subj-row head"><span></span><span>Primary</span><span>Secondary</span><span>GCSE</span><span>A-level</span><span>University</span><span>Adult Learner</span></div>
  <div class="subj-row"><span>Biology</span><span>£20</span><span>£20</span><span>£50</span><span></span><span>£20</span><span>£20</span></div>
  <div class="subj-row"><span>Chemistry</span><span>£20</span><span>£30</span><span>£20</span><span></span><span>£20</span><span>£20</span></div>
  <div class="subj-row"><span>Chemistry</span><span>£20</span><span>£30</span><span>£20</span><span></span><span>£20</span><span>£20</span></div>
  <div class="subj-row"><span>Chemistry</span><span>£20</span><span>£30</span><span>£20</span><span></span><span>£20</span><span>£20</span></div>
</section>

<section class="abs availability">
  <div class="panel-head avail-head"><span>Availability</span><span class="month">December 2016 <svg width="44" height="14" viewBox="0 0 44 14"><path d="M6 2L1 7l5 5" fill="none" stroke="#fff" stroke-width="1.6"/><rect x="15" y="2" width="12" height="11" fill="#fff"/><rect x="15" y="2" width="12" height="3" fill="#aaa"/><path d="M38 2l5 5-5 5" fill="none" stroke="#fff" stroke-width="1.6"/></svg></span></div>
  <div class="grid">
    <div class="h"></div><div class="h">Mon (7th)</div><div class="h">Tue (8th)</div><div class="h">Wed (9th)</div><div class="h">Thu (10th)</div><div class="h">Fri (11th)</div><div class="h">Sat (12th)</div><div class="h">Sun (13th)</div>
    <div class="t">7-8PM</div><div class="a"></div><div class="a"></div><div class="tk"></div><div class="a"></div><div class="a"></div><div class="a"></div><div class="a"></div>
    <div class="t">8-9PM</div><div class="a"></div><div class="a"></div><div class="r"></div><div class="a"></div><div class="a"></div><div class="a"></div><div class="n"></div>
    <div class="t">4-5PM</div><div class="a"></div><div class="a"></div><div class="n"></div><div class="a"></div><div class="r"></div><div class="a"></div><div class="a"></div>
  </div>
  <div class="legend"><span><i style="background:var(--avail)"></i>Available</span><span><i style="background:var(--taken)"></i>Taken</span><span><i style="background:var(--reserved)"></i>Reserved</span><span><i style="background:var(--no)"></i>No</span></div>
</section>

<h2 class="abs section-title">Tutors Reviews</h2>
<div class="abs title-rule"></div>
<article class="abs review-card" style="left:74px">
  <div class="avatar" role="img" aria-label="Reviewer photo" style="background:linear-gradient(#e9d9c4,#b58f6e)"></div>
  <h4>Jackline</h4><div class="stars">★★★<span class="off">★★</span></div><small>(Star Rateing 3)</small>
  <p>" Reference site about Lorem Ipsum, giving information on its origins, as well as a random Lipsum generator."</p>
</article>
<article class="abs review-card" style="left:435px">
  <div class="avatar" role="img" aria-label="Reviewer photo" style="background:linear-gradient(#d9dde2,#5a5f6b)"></div>
  <h4>John Smith</h4><div class="stars">★★★<span class="off">★★</span></div><small>(Star Rateing 3)</small>
  <p>" Reference site about Lorem Ipsum, giving information on its origins, as well as a random Lipsum generator."</p>
</article>
<article class="abs review-card" style="left:793px">
  <div class="avatar" role="img" aria-label="Reviewer photo" style="background:linear-gradient(#e5e2dc,#6e4a36)"></div>
  <h4>Sofia</h4><div class="stars">★★★<span class="off">★★</span></div><small>(Star Rateing 3)</small>
  <p>" Reference site about Lorem Ipsum, giving information on its origins, as well as a random Lipsum generator."</p>
</article>

<footer class="abs footer">
  <div class="fcol news" style="left:72px">
    <h5>Get Our Newsletter</h5>
    <p>To receive updates about my tutor,<br>Join our newsletter.</p>
    <label>Name</label><label>Email</label>
    <div class="btn subscribe">Subscribe</div>
  </div>
  <div class="fcol" style="left:435px">
    <h5>Contact Us</h5>
    <p style="line-height:20px">47 Harbour Row,<br>Kelsey Vale, 20417</p>
    <p style="line-height:20px;margin-top:14px">T: 1800 555 01<br>E: info@lendyourlessons.com</p>
    <div class="social"><i style="background:#3b5a9a"></i><i style="background:#2aa3ef"></i><i style="background:#dc4a38"></i></div>
  </div>
  <div class="fcol" style="left:705px">
    <h5>Quick Links</h5>
    <ul><li>Home</li><li>Search</li><li>Student</li><li>Tutor</li><li>About</li><li>Contact</li></ul>
  </div>
  <div class="fcol" style="left:885px">
    <h5>Info Links</h5>
    <ul><li>Register as a Student</li><li>Register as a Paretnt</li><li>Register as a Tutor</li></ul>
  </div>
  <p class="copy">Copyright 2016 Lend Your Lessons. All Rights Reserved.</p>
</footer>
</body>
</html>
```